Business Card Design (NEW FILES)

ATTENTION: New vector files are available. Please update your design to reflect/use the new (better resolution) logo images.

Seeking a unique and professional business card design for a commercial drone photography/videography business. The layout should feature
the logo (attached) and include the following information:
Owen Tarrick
614-502-7738
www.skylarkreelworks.example
NRD Certified Remote Pilot

Owen Tarrick

```html
<!DOCTYPE html>
<html lang="en">
<head>
<meta charset="utf-8">
<title>Skylark Reelworks – Business Card</title>
<link rel="stylesheet" href="https://fonts.googleapis.com/css2?family=Open+Sans:wght@400;600;700&display=swap">
<style>
  :root {
    --orange: #ec8c55;
    --orange-deep: #d9753d;
    --orange-emboss: #f29a66;
    --navy: #1c2150;
    --white: #ffffff;
    --backdrop: #1d1d20;
    --watermark: #ececf0;
  }
  * { box-sizing: border-box; margin: 0; padding: 0; }
  html, body {
    width: 1200px; height: 780px; overflow: hidden;
    background: var(--backdrop);
    font-family: "Open Sans", Arial, sans-serif;
  }
  .canvas {
    width: 1200px; height: 780px;
    display: flex; align-items: center; justify-content: center; gap: 40px;
  }
  .card {
    position: relative;
    width: 540px; height: 309px;
    border-radius: 22px;
    overflow: hidden;
  }

  /* Front */
  .card-front { background: var(--orange); }
  .front-brand {
    position: absolute; left: 0; right: 0; top: 50%;
    transform: translateY(-50%);
    display: flex; align-items: center; justify-content: center; gap: 14px;
  }
  .front-brand .brand-dot {
    width: 30px; height: 30px; border-radius: 50%;
    background: var(--orange-emboss);
  }
  .front-brand .brand-name {
    font-weight: 600; font-size: 34px; letter-spacing: 2px;
    color: var(--orange-emboss); text-transform: uppercase;
  }

  /* Back */
  .card-back {
    background: var(--white);
    border-left: 5px solid var(--orange);
    border-bottom: 5px solid var(--orange);
  }
  .back-brand {
    position: absolute; left: 34px; top: 44px;
    display: flex; align-items: center; gap: 10px;
  }
  .back-brand .brand-dot {
    width: 20px; height: 20px; border-radius: 50%; background: var(--navy);
  }
  .back-brand .brand-name {
    font-weight: 600; font-size: 21px; letter-spacing: 1.5px;
    color: var(--navy); text-transform: uppercase;
  }
  .watermark-circle {
    position: absolute; right: 70px; top: 90px;
    width: 90px; height: 90px; border-radius: 50%;
    background: var(--watermark);
  }
  .owner {
    position: absolute; right: 46px; top: 40px; text-align: right;
  }
  .owner-name { font-size: 26px; font-weight: 700; line-height: 1.1; }
  .owner-name .first { color: var(--orange); }
  .owner-name .last { color: var(--navy); }
  .owner-role { font-size: 13px; font-weight: 600; color: var(--navy); }
  .owner-tab {
    position: absolute; right: 0; top: 40px;
    width: 22px; height: 46px; background: var(--orange);
  }
  .credentials {
    position: absolute; left: 34px; top: 122px;
    color: var(--orange); font-size: 17px; font-weight: 600; line-height: 1.3;
  }
  .contact-list {
    position: absolute; left: 34px; bottom: 26px; list-style: none;
  }
  .contact-list li {
    display: flex; align-items: center; gap: 10px;
    font-size: 14px; font-weight: 600; color: var(--navy); line-height: 1.55;
  }
  .contact-list svg { width: 14px; height: 14px; flex: none; }
</style>
</head>
<body>
<main class="canvas">
  <section class="card card-front" aria-label="Card front">
    <div class="front-brand">
      <span class="brand-dot"></span>
      <span class="brand-name">Skylark Reelworks</span>
    </div>
  </section>

  <section class="card card-back" aria-label="Card back">
    <div class="back-brand">
      <span class="brand-dot"></span>
      <span class="brand-name">Skylark Reelworks</span>
    </div>

    <div class="watermark-circle" role="img" aria-label="Faint brand emblem decoration"></div>
    <div class="owner-tab"></div>
    <div class="owner">
      <p class="owner-name"><span class="first">Owen</span> <span class="last">Tarrick</span></p>
      <p class="owner-role">Owner</p>
    </div>

    <div class="credentials">
      <p>NRD Certified Remote Pilot</p>
      <p>Fully Insured</p>
    </div>

    <ul class="contact-list">
      <li>
        <svg viewBox="0 0 24 24" aria-hidden="true"><path fill="var(--orange)" d="M6.6 10.8a15.1 15.1 0 0 0 6.6 6.6l2.2-2.2a1 1 0 0 1 1-.25 11.4 11.4 0 0 0 3.6.57 1 1 0 0 1 1 1V20a1 1 0 0 1-1 1A17 17 0 0 1 3 4a1 1 0 0 1 1-1h3.5a1 1 0 0 1 1 1c0 1.25.2 2.45.57 3.6a1 1 0 0 1-.25 1z"/></svg>
        614-502-7738
      </li>
      <li>
        <svg viewBox="0 0 24 24" aria-hidden="true"><circle cx="12" cy="12" r="9" fill="none" stroke="var(--orange)" stroke-width="2.4"/><path d="M3 12h18M12 3c3 3 3 15 0 18M12 3c-3 3-3 15 0 18" fill="none" stroke="var(--orange)" stroke-width="1.8"/></svg>
        www.skylarkreelworks.example
      </li>
      <li>
        <svg viewBox="0 0 24 24" aria-hidden="true"><rect x="2.5" y="5" width="19" height="14" rx="2" fill="none" stroke="var(--orange)" stroke-width="2.4"/><path d="M3 6l9 7 9-7" fill="none" stroke="var(--orange)" stroke-width="2.2"/></svg>
        info@skylarkreelworks.example
      </li>
    </ul>
  </section>
</main>
</body>
</html>
```